Stationery Design Project for Nimbora, Chicago

Nimbora, a street parking application which helps car drivers find a street parking spot by offering an ideal path along which to look for parking. This path is calculated by our algorithm based on data (e.g. historical data, baseball games schedule, etc.). Along this path the driver will find a spot and will also save 70% of the search time. Customer we target is reg. between 21 and 45 yo.

We envision something young, fresh, bright and original. Slightly abstract maybe. It should represent the idea and elements of finding street parking in the city, e.g. car(s), parking spot, people, city, etc. (just ideas!).

Logo is attached.

Requirement:
- Business Cards (2 Sided Full Color CMYK)
- Letterhead (1 Sided Full Color CMYK)
- Envelope (1 Sided Full Color CMYK)
- Sticker (1 Sided Full Color CMYK), round with a 2inch diameter.

Reason: We're starting to get more and more designs and need more time to look into all of them. Very exciting!! Thanks to everybody!

Hi all, we're in the process of selecting our favs. Though choices!!! Really good submissions. Will keep you posted and sorry for the delay.

Target Market(s)

Car drivers and owners between 21 and 45

Industry/Entity Type

Parking

Requirements
Must have
• Sticker should be round and include company URL nimbora.com and the new logo which we will attach soon.
Should not have
• Should not be too serious or boring.

```html
<!DOCTYPE html>
<html lang="en">
<head>
<meta charset="utf-8">
<title>Nimbora Business Card</title>
<link href="https://fonts.googleapis.com/css2?family=Open+Sans:wght@400;600;700&display=swap" rel="stylesheet">
<style>
  :root {
    --page-bg: #e6e6e6;
    --card-blue: #2e3592;
    --tab-blue: #29a8e0;
    --mark-blue: #1f4fc4;
    --white: #ffffff;
    --band-top: #4a4a4a;
    --band-mid: #1c1c1c;
    --band-bottom: #000000;
    --ink-dark: #1a1a1a;
    --sky: #e9ecef;
    --trees: #5e7a55;
    --asphalt: #5d5f62;
  }
  * { box-sizing: border-box; margin: 0; padding: 0; }
  html, body { width: 956px; height: 1200px; overflow: hidden; }
  body {
    background: var(--page-bg);
    font-family: "Open Sans", Arial, sans-serif;
    position: relative;
  }
  .card {
    position: absolute;
    left: 96px;
    width: 798px;
    height: 456px;
    border-radius: 28px;
    overflow: hidden;
    box-shadow: 0 6px 18px rgba(0,0,0,0.25);
  }
  /* Front */
  .card-front { top: 112px; background: var(--card-blue); }
  .top-tab {
    position: absolute; left: 284px; top: 0;
    width: 254px; height: 12px;
    background: var(--tab-blue);
    border-radius: 0 0 10px 10px;
  }
  .brand {
    position: absolute; display: flex; align-items: center;
  }
  .brand-front { left: 86px; top: 73px; gap: 36px; }
  .brand-dot {
    border-radius: 50%;
    background: radial-gradient(circle at 40% 35%, #4f86ff, var(--mark-blue) 60%, #16338a);
  }
  .brand-front .brand-dot { width: 170px; height: 170px; }
  .brand-name { font-weight: 600; line-height: 1; }
  .brand-front .brand-name { color: var(--white); font-size: 96px; letter-spacing: 1px; }
  .holder { position: absolute; left: 50px; top: 300px; color: var(--white); }
  .holder-name { font-size: 24px; font-weight: 700; line-height: 1.2; }
  .holder-role { font-size: 18px; font-weight: 700; margin-top: 2px; }
  .address {
    position: absolute; right: 30px; top: 306px;
    color: var(--white); text-align: right;
    font-size: 19px; line-height: 27px;
  }
  .contact-band {
    position: absolute; left: 0; bottom: 0;
    width: 100%; height: 81px;
    background: linear-gradient(180deg, var(--band-top) 0%, var(--band-mid) 45%, var(--band-bottom) 100%);
    color: var(--white); font-size: 19px; line-height: 27px;
  }
  .contact-left { position: absolute; left: 50px; top: 12px; }
  .contact-right { position: absolute; right: 32px; top: 12px; text-align: right; }
  .contact-band b { font-weight: 700; }
  /* Back */
  .card-back { top: 637px; }
  .scene-photo {
    position: absolute; inset: 0;
    background: linear-gradient(180deg,
      var(--sky) 0%, var(--sky) 28%,
      var(--trees) 34%, #7d8f6e 48%,
      var(--asphalt) 56%, #707276 75%, #55575a 100%);
  }
  .brand-back { left: 206px; top: 22px; gap: 18px; }
  .brand-back .brand-dot { width: 106px; height: 106px; box-shadow: 0 0 0 4px rgba(255,255,255,0.6); }
  .brand-back .brand-name { color: var(--ink-dark); font-size: 64px; }
</style>
</head>
<body>
  <section class="card card-front">
    <div class="top-tab"></div>
    <div class="brand brand-front">
      <span class="brand-dot"></span>
      <span class="brand-name">Nimbora</span>
    </div>
    <div class="holder">
      <p class="holder-name">Your Name</p>
      <p class="holder-role">Designation</p>
    </div>
    <div class="address">
      <p>City Name, Street Name</p>
      <p>State Name, Country Code</p>
    </div>
    <div class="contact-band">
      <div class="contact-left">
        <p><b>t</b> : 123-456-7890</p>
        <p><b>c</b> : 123-456-7890</p>
      </div>
      <div class="contact-right">
        <p><b>e</b> : name@website.com</p>
        <p><b>w</b> : www.website.com</p>
      </div>
    </div>
  </section>

  <section class="card card-back">
    <div class="scene-photo" role="img" aria-label="Photo of a large open-air car park full of parked cars, with trees and buildings behind under a pale sky"></div>
    <div class="brand brand-back">
      <span class="brand-dot"></span>
      <span class="brand-name">Nimbora</span>
    </div>
  </section>
</body>
</html>
```